Falkrin homes and renovations business card design.

Would like some new card designs utilizing my new logo that look professional. I am open to different colors on the logo or utilize the same ones we have. I like the original concept but would like to see some fresh ideas and build on what we have already done.

Target Market(s)

Custom home building industry, Real estate sales, Renovation projects.

Industry/Entity Type

Home Builder

Contact Information for Business Card

Falkrin Homes and Renovations
2871 96th Avenue
Brenmoor, Westvale
T2R3W8
Home : 403- 718-4063 Cell: 403- 294-5170

My info is : Dax Falkrin, President and CEO
email: falkrinhomes@maildrop-example.net
Website: falkrinhomes-example.com
websit

Requirements
Must have
• Must Use my new logo design. I am open to different colors on the logo or utilize the same ones in the existing design. I can upload the original logo design if needed.

```html
<!DOCTYPE html>
<html lang="en">
<head>
<meta charset="utf-8">
<title>Falkrin Homes and Renovations – Business Card</title>
<link rel="stylesheet" href="https://fonts.googleapis.com/css2?family=Montserrat:wght@300;400;500;600&display=swap">
<style>
  :root {
    --backdrop: #d9dadc;
    --card-white: #ffffff;
    --card-dark: #3f3f41;
    --ink: #3a3a3c;
    --ink-soft: #555557;
    --accent: #f5b51c;
    --brand-gold: #b98a2e;
  }
  * { box-sizing: border-box; margin: 0; padding: 0; }
  html, body { width: 1200px; height: 800px; overflow: hidden; }
  body {
    background: var(--backdrop);
    font-family: "Montserrat", sans-serif;
    position: relative;
  }
  .card {
    position: absolute;
    left: 345px;
    width: 638px;
    height: 354px;
    transform: scale(0.8);
    transform-origin: top left;
    border-radius: 20px;
    overflow: hidden;
    background: var(--card-white);
  }
  .card--front { top: 69px; }
  .card--back { top: 409px; }
  .card__shape { position: absolute; inset: 0; width: 638px; height: 354px; }

  .holder { position: absolute; left: 52px; top: 16px; width: 190px; text-align: center; }
  .holder__name { font-size: 29px; font-weight: 600; color: var(--ink); letter-spacing: 0.3px; white-space: nowrap; }
  .holder__title { font-size: 17px; font-weight: 400; color: var(--ink-soft); margin-top: 1px; letter-spacing: 0.4px; }

  .contact { position: absolute; left: 50px; top: 112px; list-style: none; }
  .contact__item { display: flex; align-items: center; color: var(--ink); font-size: 15px; font-weight: 400; line-height: 20px; letter-spacing: 0.3px; white-space: nowrap; }
  .contact__item + .contact__item { margin-top: 10px; }
  .contact__item--email { font-size: 12px; letter-spacing: 0; }
  .contact__item--web { font-size: 13px; letter-spacing: 0.1px; }
  .contact__icon {
    flex: 0 0 30px; width: 30px; height: 30px; border-radius: 50%;
    background: var(--accent); margin-right: 14px;
    display: flex; align-items: center; justify-content: center;
  }
  .contact__icon svg { width: 16px; height: 16px; }

  .brand { position: absolute; color: var(--brand-gold); font-weight: 500; text-align: left; }
  .brand__name { display: block; line-height: 1; }
  .brand__line { display: block; letter-spacing: 0.6px; }
  .brand--small { left: 439px; top: 186px; }
  .brand--small .brand__name { font-size: 25px; letter-spacing: 0.5px; }
  .brand--small .brand__line { font-size: 8px; margin-top: 2px; }
  .brand--large { left: 52px; top: 170px; }
  .brand--large .brand__name { font-size: 41px; letter-spacing: 0.6px; }
  .brand--large .brand__line { font-size: 13.5px; margin-top: 3px; }
</style>
</head>
<body>

<section class="card card--front" aria-label="Business card front">
  <svg class="card__shape" viewBox="0 0 638 354" aria-hidden="true">
    <defs>
      <linearGradient id="silver-front" x1="0" y1="0" x2="1" y2="0">
        <stop offset="0" stop-color="#9a9a9c"/>
        <stop offset="0.45" stop-color="#f4f4f5"/>
        <stop offset="0.7" stop-color="#8a8a8c"/>
        <stop offset="1" stop-color="#d6d6d8"/>
      </linearGradient>
    </defs>
    <path d="M274 0 C336 60 392 150 382 230 C375 295 352 325 358 354 L638 354 L638 0 Z" fill="var(--card-dark)"/>
    <path d="M266 0 C328 60 384 150 374 230 C367 295 344 325 350 354" fill="none" stroke="url(#silver-front)" stroke-width="14"/>
  </svg>

  <div class="holder">
    <p class="holder__name">Dax Falkrin</p>
    <p class="holder__title">President</p>
  </div>

  <ul class="contact">
    <li class="contact__item">
      <span class="contact__icon"><svg viewBox="0 0 16 16"><rect x="4.5" y="1.5" width="7" height="13" rx="1.2" fill="none" stroke="#fff" stroke-width="1.4"/><line x1="7" y1="12.3" x2="9" y2="12.3" stroke="#fff" stroke-width="1.2"/></svg></span>
      <span>403- 718-4063<br>403- 294-5170</span>
    </li>
    <li class="contact__item">
      <span class="contact__icon"><svg viewBox="0 0 16 16"><path d="M8 15 C4 10 3 8 3 6 A5 5 0 0 1 13 6 C13 8 12 10 8 15 Z" fill="#fff"/><circle cx="8" cy="6" r="1.8" fill="var(--accent)"/></svg></span>
      <span>2871 96th Avenue<br>Brenmoor, Westvale</span>
    </li>
    <li class="contact__item contact__item--email">
      <span class="contact__icon"><svg viewBox="0 0 16 16"><rect x="2" y="3.5" width="12" height="9" fill="none" stroke="#fff" stroke-width="1.3"/><path d="M2 3.5 L8 9 L14 3.5 M2 12.5 L6.5 7.8 M14 12.5 L9.5 7.8" fill="none" stroke="#fff" stroke-width="1.1"/></svg></span>
      <span>falkrinhomes@maildrop-example.net</span>
    </li>
    <li class="contact__item contact__item--web">
      <span class="contact__icon"><svg viewBox="0 0 16 16"><circle cx="8" cy="8" r="6.3" fill="none" stroke="#fff" stroke-width="1.3"/><ellipse cx="8" cy="8" rx="2.8" ry="6.3" fill="none" stroke="#fff" stroke-width="1"/><line x1="1.7" y1="8" x2="14.3" y2="8" stroke="#fff" stroke-width="1"/></svg></span>
      <span>www.falkrinhomes-example.com</span>
    </li>
  </ul>

  <p class="brand brand--small">
    <span class="brand__name">FALKRIN</span>
    <span class="brand__line">HOMES AND RENOVATIONS</span>
  </p>
</section>

<section class="card card--back" aria-label="Business card back">
  <svg class="card__shape" viewBox="0 0 638 354" aria-hidden="true">
    <defs>
      <linearGradient id="silver-back" x1="0" y1="0" x2="1" y2="0">
        <stop offset="0" stop-color="#8c8c8e"/>
        <stop offset="0.45" stop-color="#f4f4f5"/>
        <stop offset="0.75" stop-color="#8a8a8c"/>
        <stop offset="1" stop-color="#d2d2d4"/>
      </linearGradient>
    </defs>
    <path d="M0 0 L358 0 C420 60 420 125 392 185 C355 262 332 300 340 354 L0 354 Z" fill="var(--card-dark)"/>
    <path d="M364 0 C426 60 426 125 398 185 C361 262 338 300 346 354" fill="none" stroke="url(#silver-back)" stroke-width="14"/>
  </svg>

  <p class="brand brand--large">
    <span class="brand__name">FALKRIN</span>
    <span class="brand__line">HOMES AND RENOVATIONS</span>
  </p>
</section>

</body>
</html>
```